Social Media App Needs PPT Template

We need a PowerPoint template for a new social media company based in the DC area called "Bold Ledger." We provide an interactive digital platform for executives to share actionable advice. We would like to see designs that use our orange logo color as an accent, but are mainly grey, white, and black. The final design should communicate clean, chic, modern, and professional.

Target Market(s)

Executives

Industry/Entity Type

Information Technology

Font styles to use
Sans Serif

Colors
f78f20
fbe7d2
ffffff
000000
e8e8e8
757575

Requirements
Must have
• My project must have title page and many options for the body of the ppt (graphs, tables, etc). It also needs to be easy to modify. I must have someone who is experienced in creating powerpoint templates.
Nice to have
• It would be nice to have a very modern and clean design that includes the logo on every page, but still leaves a lot of room for the content of the slide
Should not have
• My design project should not look to busy.

```html
<!DOCTYPE html>
<html lang="en">
<head>
<meta charset="utf-8">
<title>Bold Ledger – About Our Company</title>
<link href="https://fonts.googleapis.com/css2?family=Lato:ital,wght@0,300;0,400;0,700;1,700&display=swap" rel="stylesheet">
<style>
  :root {
    --stage: #919191;
    --orange: #e8861a;
    --orange-light: #ef9a2e;
    --charcoal: #474747;
    --ink: #3a3a3a;
    --white: #ffffff;
    --placeholder: #cbcccf;
    --footer-text: #d6d6d6;
  }
  * { margin: 0; padding: 0; box-sizing: border-box; }
  html, body {
    width: 1200px; height: 960px; overflow: hidden;
    background: var(--stage);
    font-family: "Lato", sans-serif;
  }
  .page-label {
    position: absolute; top: 44px; left: 0; width: 1200px;
    text-align: center; color: var(--white);
    font-weight: 300; font-size: 25px;
  }
  .slide {
    position: absolute; left: 87px; top: 128px;
    width: 1046px; height: 784px; overflow: hidden;
    background: radial-gradient(ellipse at 50% 35%, #ffffff 0%, #f6f6f6 55%, #ececec 100%);
  }
  .header-shapes { position: absolute; left: 0; top: 0; }
  .slide-title {
    position: absolute; left: 32px; top: 69px;
    color: var(--white); font-weight: 300; font-size: 38px; line-height: 1;
  }
  .brand {
    position: absolute; left: 848px; top: 76px;
    display: flex; align-items: center; gap: 9px;
  }
  .brand-dot { width: 16px; height: 16px; border-radius: 50%; background: var(--orange); }
  .brand-name { color: var(--white); font-weight: 700; font-size: 22px; line-height: 1; }
  .column {
    position: absolute; top: 212px;
    font-size: 16.8px; line-height: 20.9px; color: var(--ink);
    text-align: justify; hyphens: auto;
  }
  .column-left { left: 37px; width: 467px; }
  .column-right { left: 547px; width: 451px; }
  .lead {
    color: var(--orange); font-weight: 700; font-style: italic;
    font-size: 17.6px; line-height: 22.6px; margin-bottom: 19px;
  }
  .column p + p { margin-top: 20px; }
  .image-placeholder {
    position: absolute; left: 549px; top: 381px; width: 446px; height: 281px;
    background: var(--placeholder);
    display: flex; align-items: center; justify-content: center;
    color: #e2e3e5; font-weight: 300; font-size: 32px;
  }
  .footer-shapes { position: absolute; left: 0; top: 742px; }
  .footer-text {
    position: absolute; left: 28px; top: 750px;
    color: var(--footer-text); font-size: 14px; line-height: 16px;
  }
  .footer-text .sep { margin: 0 7px; }
</style>
</head>
<body>
  <div class="page-label">Page 3</div>

  <section class="slide">
    <svg class="header-shapes" width="1046" height="150" viewBox="0 0 1046 150" aria-hidden="true">
      <polygon points="0,49 793,49 712,130 0,130" fill="var(--orange)"/>
      <polygon points="600,49 793,49 730,112 560,112" fill="var(--orange-light)" opacity="0.45"/>
      <polygon points="0,49 793,49 776,66 0,66" fill="var(--orange-light)" opacity="0.35"/>
      <polygon points="801,49 1046,49 1046,130 713,130" fill="var(--charcoal)"/>
      <polygon points="818,34 1046,34 1046,44 808,44" fill="var(--orange)"/>
      <polygon points="0,135 705,135 694,145 0,145" fill="var(--charcoal)"/>
    </svg>
    <h1 class="slide-title">About Our Company</h1>
    <div class="brand">
      <span class="brand-dot"></span>
      <span class="brand-name">Bold Ledger</span>
    </div>

    <div class="column column-left">
      <p class="lead">Lorem ipsum dolor sit amet, consectetuer adipiscing elit, sed diam nonummy nibh euismod tincidunt ut laoreet dolore magna aliquam erat volutpat. Ut wisi enim ad minim veniam, quis nostrud exerci tation ullamcorper suscipit lobortis nisl ut aliquip ex ea commodo consequat.</p>
      <p>Duis autem vel eum iriure dolor in hendrerit in vulputate velit esse molestie consequat, vel illum dolore eu feugiat nulla facilisis at vero eros et accumsan et iusto odio dignissim qui blandit praesent luptatum zzril delenit augue duis dolore te feugait nulla facilisi. Nam liber tempor cum soluta nobis eleifend option congue nihil imperdiet doming id quod mazim placerat facer possim assum. Typi non habent claritatem insitam; est usus legentis in iis qui facit eorum claritatem. Investigationes demonstraverunt lectores legere me lius quod ii legunt saepius. Claritas est etiam processus dynamicus, qui sequitur mutationem consuetudium lectorum.</p>
      <p>Typi non habent claritatem insitam; est usus legentis in iis qui facit eorum claritatem. Investigationes.</p>
    </div>

    <div class="column column-right">
      <p>Duis autem vel eum iriure dolor in hendrerit in vulputate velit esse molestie consequat, vel illum dolore eu feugiat nulla facilisis at vero eros et accumsan et iusto odio dignissim qui blandit praesent luptatum zzril delenit augue duis dolore te feugait nulla facilisi. Nam liber tempor cum soluta nobis eleifend option congue nihil imperdiet doming id quod mazim placerat facer possim assum.</p>
    </div>

    <div class="image-placeholder" role="img" aria-label="Photo placeholder for a company image">Image Goes Here</div>

    <svg class="footer-shapes" width="1046" height="31" viewBox="0 0 1046 31" aria-hidden="true">
      <polygon points="0,0 298,0 267,31 0,31" fill="var(--charcoal)"/>
      <polygon points="303,0 1046,0 1046,31 272,31" fill="var(--orange)"/>
    </svg>
    <p class="footer-text">www.boldledger.com<span class="sep">|</span>Page 1</p>
  </section>
</body>
</html>
```